Logo for a Food & Beverage Franchise Company

We need a logo and stationary for a new company that just aquired a restaurant franchise. We need a sleep and professional logo with stationary.

Target Market(s)

Adults, resturaunt owners, franchisors (Companies who own food franchise companies such as Farrowbys Head Office, Toastwell International Franchise)
and Big Food and Beverage who wish to give franchise rights to us)

Industry/Entity Type

Restaurant

Logo Text

Velvet Harbor

Logo styles of interest
Emblem Logo
Pictorial/Combination Logo
Character Logo
Font styles to use
Serif
Sans Serif

Colors
ffc214
f78f20
f37022
faa54b
fece3e
fbed22

Requirements
Must have
• Maximum three color. The less the better.
Nice to have
• It does not have to have a crown, but if you wish to have a crown then it does not have to be so sharp and clear. Abstract is better.

```html
<!DOCTYPE html>
<html lang="en">
<head>
<meta charset="utf-8">
<title>Velvet Harbor – Business Cards</title>
<link rel="stylesheet" href="https://fonts.googleapis.com/css2?family=Montserrat:wght@500&family=Open+Sans:wght@400;600&display=swap">
<style>
  :root {
    --backdrop: #ececec;
    --card: #2b2b2b;
    --card-edge: #1f1f1f;
    --gold: #c9a75a;
    --ivory: #eee6d2;
  }
  * { margin: 0; padding: 0; box-sizing: border-box; }
  html, body { width: 1200px; height: 800px; overflow: hidden; background: var(--backdrop); }
  .canvas { position: relative; width: 1200px; height: 800px; }

  .card {
    position: absolute;
    width: 460px;
    height: 262px;
    background: var(--card);
    border-radius: 3px;
    box-shadow: 0 2px 0 var(--card-edge), 0 14px 30px rgba(0,0,0,0.18);
    overflow: hidden;
  }
  .card--back { left: 170px; top: 110px; }
  .card--front { left: 570px; top: 410px; }

  .wordmark {
    font-family: "Montserrat", sans-serif;
    font-weight: 500;
    color: var(--gold);
    text-transform: uppercase;
    white-space: nowrap;
  }
  .card--back .wordmark {
    position: absolute; left: 0; right: 0; top: 50%;
    transform: translateY(-50%);
    text-align: center;
    font-size: 30px;
    letter-spacing: 0.22em;
  }

  .lockup {
    position: absolute; left: 150px; top: 78px;
    display: flex; align-items: center; gap: 10px;
  }
  .lockup__square { width: 10px; height: 10px; background: var(--gold); }
  .lockup .wordmark { font-size: 13px; letter-spacing: 0.28em; }

  .contact {
    position: absolute; left: 34px; bottom: 30px;
    font-family: "Open Sans", sans-serif;
    font-size: 11px; line-height: 1.45;
    color: var(--gold);
  }
  .contact__name, .contact__role { color: var(--ivory); font-weight: 600; }
  .contact__role { margin-bottom: 12px; }
</style>
</head>
<body>
<main class="canvas">
  <section class="card card--back" aria-label="Business card, back">
    <div class="wordmark">Velvet Harbor</div>
  </section>

  <section class="card card--front" aria-label="Business card, front">
    <div class="lockup">
      <span class="lockup__square"></span>
      <span class="wordmark">Velvet Harbor</span>
    </div>
    <address class="contact" style="font-style: normal;">
      <div class="contact__name">Karim Haddad</div>
      <div class="contact__role">C.E.O.</div>
      <div>Office: +000 4 555 0142</div>
      <div>Mobile: +000 50 555 0199</div>
      <div>Email: karim@velvetharbor.com</div>
      <div>P.O. Box 1180, Harbor City</div>
      <div>www.velvetharborfood.com</div>
    </address>
  </section>
</main>
</body>
</html>
```